Mortgage and Asset Finance Broker Needs a Wordpress Website Design

I need a modern looking Wordpress website to showcase my service as a mortgage and asset broker. I have a company and we work with various lenders to arrange mortgages, as well as commercial lending and business asset finance. The website needs to look professional, be easy to navigate and capture leads. SEO is obviously very important to me. It really needs to be something that shows trust and professioanlism.
Updates

On the home page I will need to have some boxes for Home Loans, Refinancing, Business (and Agriculture) Loans etc. I'd like a carousel in the middle which shows our lenders (so that can have the banks logos added).

It needs to be easy top navigate and showcase all we do - Home Loans, Refinancing, Commercial Loans, Car Loans, Asset Finance etc.

There are plenty of companies on the internet that do this.

There is some good information here https://lendplatehq.com.au/mortgage-broker-homepage/

I need to make sure that editing the website is easy (I think Wordpress has something that allows that).

Also we are very much an Australian business so that is something to advertise.

Industry/Entity Type

Mortgage and Finance Broker

Coding

Coded - Design and coding required

Number of Pages Required

5+ page

Requirements
Must have
• Easy to navigate professional feel. Must be responsive and mobile friendly.
Nice to have
• Homepage with links to inner pages. Contact buttons.

```html
<!DOCTYPE html>
<html lang="en">
<head>
<meta charset="utf-8">
<title>Keystone Financial Services — Mortgage &amp; Asset Finance</title>
<link href="https://fonts.googleapis.com/css2?family=Comfortaa:wght@600;700&family=Montserrat:wght@400;500;600;700&display=swap" rel="stylesheet">
<style>
:root{
  --blue:#0b57a4;
  --navy:#0d3c78;
  --pink:#e4256b;
  --orange:#f5902a;
  --purple:#7b3590;
  --ink:#1b1b1b;
  --text:#555a60;
  --light-blue:#dcecfb;
  --line:#e3e6ea;
  --head:"Comfortaa",sans-serif;
  --body:"Montserrat",sans-serif;
}
*{box-sizing:border-box;margin:0;padding:0}
html,body{width:1200px;height:3966px;overflow:hidden}
body{position:relative;background:#fff;font-family:var(--body);color:var(--ink)}
.abs{position:absolute}
.btn{position:absolute;display:flex;align-items:center;justify-content:center;background:var(--orange);color:#fff;font:600 13px var(--body);border-radius:22px;letter-spacing:.2px}
.h-title{font-family:var(--head);font-weight:700;color:var(--ink)}
.h-title .hl{color:var(--blue)}
.round-arrow{position:absolute;width:44px;height:44px;border-radius:50%;border:2px solid #9aa0a6;background:#fff;display:flex;align-items:center;justify-content:center}

.topbar{position:absolute;left:0;top:0;width:1200px;height:44px}
.topbar .call{left:145px;top:11px;color:#fff;font:700 17px var(--body);display:flex;align-items:center;gap:10px}
.topbar .mail{left:765px;top:13px;color:#fff;font:600 14px var(--body);display:flex;align-items:center;gap:6px;white-space:nowrap}
.social-dot{position:absolute;top:11px;width:22px;height:22px;border-radius:50%;border:2px solid #fff}

.logo{position:absolute;display:flex;align-items:center;gap:10px}
.logo .mark{width:42px;height:42px;background:var(--orange);border-radius:4px}
.logo .name{font:700 34px var(--body);color:var(--ink);line-height:1}
.logo .sub{font:600 11px var(--body);color:var(--ink);letter-spacing:.5px}
.nav a{position:absolute;top:79px;font:500 14px var(--body);color:var(--ink);text-decoration:none}

.hero{position:absolute;left:0;top:138px;width:1200px;height:550px;overflow:hidden;background:#eef0f3}
.hero-card{position:absolute;left:570px;top:112px;width:486px;height:357px;background:rgba(255,255,255,.94)}
.hero-card h1{position:absolute;left:42px;top:36px;font:700 42px/44px var(--head);color:var(--blue);white-space:nowrap}
.hero-card h1 span{color:var(--ink)}
.hero-card p{position:absolute;left:42px;top:182px;font:500 21px/31px var(--body);color:var(--ink)}
.dot{position:absolute;left:1121px;width:10px;height:10px;border-radius:50%;background:#8a8f96}

.apply{position:absolute;left:0;top:688px;width:1200px;height:145px;background:#fff;box-shadow:0 8px 14px rgba(0,0,0,.06)}
.apply h2{position:absolute;left:170px;top:15px;font:700 42px/50px var(--head);color:var(--ink)}
.apply h2 .hl{color:var(--blue)}
.field{position:absolute;top:22px;width:184px;height:41px;border:1px solid #aeb3b8;font:400 12px var(--body);color:#444;padding:13px 20px}
.consent{position:absolute;left:458px;top:93px;font:400 11px var(--body);color:#333;display:flex;align-items:center;gap:8px}
.consent i{width:10px;height:10px;border:1px solid #555;display:block}

.cat-label{position:absolute;width:180px;text-align:center;font:600 13px/21px var(--body);color:var(--ink)}

.about-text{position:absolute;left:583px;top:1496px;width:472px;font:400 14.2px/27.3px var(--body);color:var(--text);text-align:justify}

.lender{position:absolute;top:2011px;width:145px;height:61px;border:2px solid #c9ccd0;border-radius:3px;display:flex;align-items:center;justify-content:center;gap:6px;font:700 15px var(--body);color:var(--ink)}
.lender i{width:14px;height:14px;background:var(--ink);display:block}

.step-circle{position:absolute;width:90px;height:90px;border-radius:50%;border:2px solid #c5c9ce;background:#fff;display:flex;align-items:center;justify-content:center}
.badge{position:absolute;width:32px;height:32px;border-radius:50%;background:var(--blue);color:#fff;font:700 17px var(--body);display:flex;align-items:center;justify-content:center}
.step-title{position:absolute;width:240px;text-align:center;font:600 14px var(--body);color:var(--ink)}
.step-desc{position:absolute;width:200px;text-align:center;font:400 15px/21px var(--body);color:var(--text)}

.t-card{position:absolute;top:3043px;width:288px;height:194px;background:#fff;border:1px solid #ddd}
.t-card .avatar{position:absolute;left:18px;top:18px;width:62px;height:62px;border-radius:50%;background:linear-gradient(135deg,#c8ccd2,#8e949c)}
.t-card .who{position:absolute;left:92px;top:28px;font:600 12px/22px var(--body);color:#333}
.t-card .who span{font-weight:400;color:#777}
.t-card .rating{position:absolute;right:18px;top:24px;width:86px;height:30px;background:#e7e9ec;border-radius:3px}
.t-card p{position:absolute;left:18px;top:98px;width:254px;font:400 10px/20px var(--body);color:#555}
.stars{position:absolute;left:18px;top:165px;color:var(--orange);font-size:15px;letter-spacing:3px}

.foot-head{position:absolute;font:600 15px var(--body);color:var(--ink);letter-spacing:.3px}
.foot-link{position:absolute;left:553px;font:400 13px var(--body);color:#333}
.icon-dot{position:absolute;width:40px;height:40px;border-radius:50%;display:flex;align-items:center;justify-content:center}
.vline{position:absolute;top:3512px;width:1px;height:208px;background:#d6d9dd}
.card-chip{position:absolute;top:3893px;width:30px;height:20px;border-radius:3px}
.soc{position:absolute;top:3885px;width:36px;height:36px;border-radius:50%}
</style>
</head>
<body>

<div class="topbar">
  <svg class="abs" style="left:0;top:0" width="1200" height="44">
    <polygon points="0,0 520,0 558,44 0,44" fill="var(--blue)"/>
    <polygon points="560,0 1200,0 1200,44 530,44" fill="var(--pink)"/>
  </svg>
  <div class="abs call">
    <svg width="26" height="26" viewBox="0 0 26 26"><circle cx="13" cy="13" r="13" fill="#fff"/><path d="M9 7l3 0 1 4-2 1.5c1 2 2.5 3.5 4.5 4.5L17 15l4 1v3c-7 0-12-5-12-12z" fill="var(--blue)" transform="translate(-2,0) scale(.95)"/></svg>
    CALL US : +1 555 010 2040
  </div>
  <div class="abs mail">
    <svg width="18" height="18" viewBox="0 0 18 18"><circle cx="9" cy="9" r="9" fill="#fff"/><rect x="4.5" y="5.5" width="9" height="7" fill="none" stroke="var(--pink)" stroke-width="1.4"/><path d="M4.5 5.5l4.5 4 4.5-4" fill="none" stroke="var(--pink)" stroke-width="1.4"/></svg>
    info@keystonefin.com
  </div>
  <span class="social-dot" style="left:976px"></span>
  <span class="social-dot" style="left:1003px"></span>
  <span class="social-dot" style="left:1031px"></span>
</div>

<div class="logo" style="left:145px;top:52px">
  <span class="mark"></span>
  <div><div class="name">Keystone</div><div class="sub">FINANCIAL SERVICES</div></div>
</div>
<nav class="nav">
  <a style="left:458px">HOME</a>
  <a style="left:538px">ABOUT US</a>
  <a style="left:648px">SERVICES</a>
  <a style="left:753px">RESOURCES</a>
  <a style="left:876px">CONTACT</a>
</nav>
<div class="btn" style="left:963px;top:67px;width:93px;height:42px;font-size:14px">LOGIN</div>

<section class="hero">
  <div role="img" aria-label="Smiling woman in a denim shirt checking her phone in a bright office" class="abs" style="left:0;top:0;width:640px;height:550px;background:linear-gradient(120deg,#c9d6e2 0%,#9fb4c8 45%,#d9dde2 100%)"></div>
  <svg class="abs" style="left:0;top:0" width="1200" height="550">
    <polygon points="500,0 670,0 860,230 690,230" fill="var(--blue)"/>
    <polygon points="1035,0 1200,0 1200,40 1010,230 880,230" fill="var(--pink)"/>
    <polygon points="540,550 690,370 860,370 720,550" fill="var(--purple)"/>
    <polygon points="880,370 1060,370 1200,440 1200,550 1000,550" fill="var(--orange)"/>
    <polygon points="1060,370 1200,220 1200,440" fill="var(--orange)" opacity=".85"/>
  </svg>
  <div class="hero-card">
    <h1>Expert Mortgage &amp;<br><span>Asset Finance</span><br>Solutions</h1>
    <p>REQUEST A LINE OF CREDIT<br>OF UP TO $2,000 TODAY!</p>
    <div class="btn" style="left:42px;top:268px;width:253px;height:42px">GET A FREE CONSULTATION</div>
  </div>
  <span class="dot" style="top:262px"></span>
  <span class="dot" style="top:286px;background:var(--blue)"></span>
  <span class="dot" style="top:310px"></span>
</section>

<section class="apply">
  <h2><span class="hl">Apply for</span><br>Your Loan</h2>
  <div class="field" style="left:462px">First Name</div>
  <div class="field" style="left:654px">Enter Email</div>
  <div class="field" style="left:846px">State</div>
  <div class="consent"><i></i>I consent and agree to the website Privacy Policy and Terms of Use. *</div>
  <div class="btn" style="left:889px;top:81px;width:140px;height:40px">APPLY NOW</div>
</section>

<h2 class="h-title abs" style="left:0;top:914px;width:1200px;text-align:center;font-size:40px"><span class="hl">Loan</span> Categories</h2>
<svg class="abs" style="left:0;top:1005px" width="1200" height="205">
  <g fill="none" stroke="#e6e9ec" stroke-width="5">
    <polygon points="193,5 405,5 346,200 119,200"/>
    <polygon points="645,5 857,5 798,200 571,200"/>
    <polygon points="871,5 1083,5 1024,200 797,200"/>
  </g>
  <polygon points="408,3 634,3 575,203 340,203" fill="var(--pink)"/>
</svg>
<div class="round-arrow" style="left:80px;top:1096px"><svg width="14" height="14"><path d="M10 1L4 7l6 6" fill="none" stroke="#555" stroke-width="2"/></svg></div>
<div class="round-arrow" style="left:1075px;top:1096px"><svg width="14" height="14"><path d="M4 1l6 6-6 6" fill="none" stroke="#555" stroke-width="2"/></svg></div>
<svg class="abs" style="left:228px;top:1045px" width="68" height="68" viewBox="0 0 68 68" fill="none" stroke="var(--navy)" stroke-width="2.4"><path d="M16 30L38 10l22 20M22 26v22h32V26"/><circle cx="38" cy="34" r="8"/><path d="M4 46h12l10 6h14l-12 10H4"/></svg>
<svg class="abs" style="left:450px;top:1050px" width="80" height="60" viewBox="0 0 80 60" fill="none" stroke="#fff" stroke-width="2.4"><path d="M4 40V28l8-14h30l8 14v12H4z"/><circle cx="14" cy="40" r="5"/><circle cx="40" cy="40" r="5"/><path d="M52 14l14-6 12 6v14c0 12-12 18-12 18S54 40 54 28"/><path d="M60 26l5 5 8-9"/></svg>
<svg class="abs" style="left:662px;top:1045px" width="70" height="70" viewBox="0 0 70 70" fill="none" stroke="var(--navy)" stroke-width="2.4"><path d="M6 40L26 24l20 16M12 36v26h28V36"/><rect x="22" y="46" width="8" height="16"/><circle cx="50" cy="20" r="12"/><path d="M50 13v14M46 16h6a3 3 0 010 6h-4a3 3 0 000 6h6"/><path d="M4 12h16l-4-4M20 12l-4 4"/></svg>
<svg class="abs" style="left:906px;top:1048px" width="64" height="64" viewBox="0 0 64 64" fill="none" stroke="var(--navy)" stroke-width="2.4"><rect x="6" y="6" width="36" height="44"/><path d="M12 16h20M12 24h16M12 32h20"/><rect x="22" y="32" width="36" height="24"/><path d="M34 32v-6h12v6M22 42h36"/></svg>
<div class="cat-label" style="left:171px;top:1141px">HOME LOANS</div>
<div class="cat-label" style="left:381px;top:1141px;color:#fff">CAR &amp; ASSET<br>FINANCE</div>
<div class="cat-label" style="left:606px;top:1141px">REFINANCING</div>
<div class="cat-label" style="left:827px;top:1141px">BUSINESS &amp;<br>AGRICULTURE LOANS</div>

<svg class="abs" style="left:0;top:1270px" width="1200" height="730">
  <polygon points="0,93 1200,16 1200,632 0,717" fill="var(--light-blue)"/>
  <polygon points="0,220 220,600 0,717" fill="#cfdcea"/>
  <polygon points="150,93 560,68 360,400" fill="#e6effa"/>
  <polygon points="78,81 570,56 570,60 78,91" fill="var(--blue)"/>
  <polygon points="570,655 1122,599 1122,609 570,665" fill="var(--navy)"/>
</svg>
<div role="img" aria-label="Smiling couple meeting a finance advisor at a desk" class="abs" style="left:148px;top:1436px;width:388px;height:388px;border-radius:50%;background:radial-gradient(circle at 45% 45%,#c7c1b8,#6f7b86)"></div>
<h2 class="h-title abs" style="left:582px;top:1426px;font-size:40px"><span class="hl">About</span> Us</h2>
<p class="about-text">Sed ut perspiciatis unde omnis iste natus error sit voluptatem accusantium doloremque laudantium, totam rem aperiam, eaque ipsa quae ab illo inventore veritatis et quasi architecto beatae vitae dicta sunt explicabo. Nemo enim ipsam voluptatem quia voluptas sit aspernatur aut odit aut fugit, sed quia consequuntur magni dolores eos qui ratione voluptatem sequi nesci porro quis qui dolorem ipsum quia dolor sitelit, sed quia non numquam eius modi tempora incidunt ut labore et dolore magnam aliquam quaerat voluptatem.</p>
<div class="btn" style="left:584px;top:1771px;width:140px;height:40px">READ MORE</div>

<h2 class="h-title abs" style="left:142px;top:2024px;font-size:33px"><span class="hl">Our</span> Lenders</h2>
<div class="round-arrow" style="left:374px;top:2026px;width:33px;height:33px"><svg width="12" height="12"><path d="M8 1L3 6l5 5" fill="none" stroke="#555" stroke-width="2"/></svg></div>
<div class="lender" style="left:431px"><i></i>Northgate</div>
<div class="lender" style="left:591px"><i></i>Harbour Bank</div>
<div class="lender" style="left:751px;font-size:12px;letter-spacing:2px"><i></i>MERIDIAN</div>
<div class="lender" style="left:912px;font-size:18px;font-weight:500"><i></i>Crestline</div>
<div class="round-arrow" style="left:1081px;top:2026px;width:33px;height:33px"><svg width="12" height="12"><path d="M4 1l5 5-5 5" fill="none" stroke="#555" stroke-width="2"/></svg></div>
<div class="abs" style="left:130px;top:2144px;width:940px;height:1px;background:var(--line)"></div>

<h2 class="h-title abs" style="left:0;top:2202px;width:1200px;text-align:center;font-size:40px"><span class="hl">How</span> it Works</h2>
<p class="abs" style="left:190px;top:2269px;width:820px;text-align:center;font:400 15px/25px var(--body);color:var(--text)">Sed ut perspiciatis unde omnis iste natus error sit voluptatem accusantium doloremque laudantium, totam rem aperiam, eaque ipsa quae ab illo inventore veritatis et quasi architecto beatae vitae dicta sunt explicabo</p>
<svg class="abs" style="left:340px;top:2410px" width="540" height="90" fill="none" stroke="#b9bec4" stroke-width="1.5" stroke-dasharray="6 5">
  <path d="M10 28C90 20 160 5 200 60"/>
  <path d="M192 52l8 10 3-13" stroke-dasharray="0"/>
  <path d="M330 50C380 36 430 70 525 30"/>
  <path d="M515 24l10 6-6 10" stroke-dasharray="0"/>
</svg>
<div class="step-circle" style="left:217px;top:2378px"><svg width="34" height="34" viewBox="0 0 34 34"><path d="M6 28l2-8L22 6l6 6-14 14z" fill="var(--blue)"/></svg></div>
<div class="badge" style="left:271px;top:2372px">1</div>
<div class="step-title" style="left:142px;top:2489px">NEMO ENIM IPSA</div>
<div class="step-desc" style="left:162px;top:2519px">Sed ut perspiciatis unde omnis iste natus error sit voluptatem accu</div>

<div class="step-circle" style="left:563px;top:2465px;border-color:var(--pink)"><svg width="30" height="34" viewBox="0 0 30 34"><path d="M4 2h14l8 8v22H4z" fill="var(--pink)"/><path d="M18 2v8h8" fill="#f7a7c4"/></svg></div>
<div class="badge" style="left:617px;top:2459px;background:var(--pink)">2</div>
<div class="step-title" style="left:488px;top:2573px">LOREMIPSUM</div>
<div class="step-desc" style="left:508px;top:2596px">Sed ut perspiciatis unde omnis iste natus error sit voluptatem accu</div>

<div class="step-circle" style="left:891px;top:2378px"><svg width="34" height="34" viewBox="0 0 34 34" fill="none" stroke="var(--blue)" stroke-width="2.6"><circle cx="17" cy="17" r="14"/><circle cx="12" cy="14" r="1" fill="var(--blue)"/><circle cx="22" cy="14" r="1" fill="var(--blue)"/><path d="M10 20c3 5 11 5 14 0"/></svg></div>
<div class="badge" style="left:947px;top:2372px">3</div>
<div class="step-title" style="left:816px;top:2489px">DOLOT SIT</div>
<div class="step-desc" style="left:836px;top:2519px">Sed ut perspiciatis unde omnis iste natus error sit voluptatem accu</div>
<div class="btn" style="left:530px;top:2696px;width:140px;height:41px">GET STARTED</div>

<svg class="abs" style="left:0;top:2775px" width="1200" height="715">
  <polygon points="0,90 1200,8 1200,590 0,709" fill="var(--purple)"/>
  <polygon points="78,77 570,50 570,56 78,90" fill="var(--orange)"/>
  <polygon points="620,612 1122,563 1122,576 620,620" fill="var(--orange)"/>
</svg>
<h2 class="abs" style="left:0;top:2948px;width:1200px;text-align:center;font:700 42px var(--head);color:#fff">Customer Testimonials</h2>
<div class="round-arrow" style="left:80px;top:3120px;border-color:#fff;background:transparent"><svg width="14" height="14"><path d="M10 1L4 7l6 6" fill="none" stroke="#fff" stroke-width="2"/></svg></div>
<div class="round-arrow" style="left:1075px;top:3120px;border-color:#fff;background:transparent"><svg width="14" height="14"><path d="M4 1l6 6-6 6" fill="none" stroke="#fff" stroke-width="2"/></svg></div>
<article class="t-card" style="left:148px">
  <div class="avatar" role="img" aria-label="Customer portrait"></div>
  <div class="who">Veritatis et<br><span>quasi beatae</span></div>
  <div class="rating"></div>
  <p>Lorem ipsum dolor sit amet, consectetur adipiscing elit, sed do eiusmod tempor incididunt ut labore et dolore magna aliquat enim ad</p>
  <div class="stars">★★★★★</div>
</article>
<article class="t-card" style="left:457px">
  <div class="avatar" role="img" aria-label="Customer portrait"></div>
  <div class="who">Veritatis et<br><span>quasi beatae</span></div>
  <div class="rating" style="width:46px;height:50px;border-radius:6px;top:18px"></div>
  <p>Lorem ipsum dolor sit amet, consectetur adipiscing elit, sed do eiusmod tempor incididunt ut labore et dolore magna aliquat enim ad</p>
  <div class="stars">★★★★★</div>
</article>
<article class="t-card" style="left:764px">
  <div class="avatar" role="img" aria-label="Customer portrait"></div>
  <div class="who">Veritatis et<br><span>quasi beatae</span></div>
  <div class="rating"></div>
  <p>Lorem ipsum dolor sit amet, consectetur adipiscing elit, sed do eiusmod tempor incididunt ut labore et dolore magna aliquat enim ad</p>
  <div class="stars">★★★★★</div>
</article>
<div class="btn" style="left:530px;top:3271px;width:140px;height:40px">VIEW MORE</div>

<div class="logo" style="left:156px;top:3515px">
  <span class="mark"></span>
  <div><div class="name" style="font-size:38px">Keystone</div><div class="sub">FINANCIAL SERVICES</div></div>
</div>
<div class="icon-dot" style="left:154px;top:3620px;border:1px solid #ddd"><svg width="18" height="16" viewBox="0 0 18 16"><path d="M1 3l5-2 6 2 5-2v12l-5 2-6-2-5 2z" fill="var(--pink)"/></svg></div>
<p class="abs" style="left:208px;top:3619px;font:400 15px/22px var(--body);color:#333">233,Sed ut perspiciatis unde<br>omnis iste natus</p>
<div class="icon-dot" style="left:154px;top:3678px;background:var(--pink)"><svg width="18" height="18" viewBox="0 0 18 18"><path d="M3 1h4l1 4-2 1.5c1 2 2.5 3.5 4.5 4.5L12 9l4 1v4c-8 0-13-5-13-13z" fill="#fff"/></svg></div>
<p class="abs" style="left:208px;top:3688px;font:400 15px var(--body);color:#333">+1 555 010 2040</p>
<div class="vline" style="left:485px"></div>
<div class="vline" style="left:678px"></div>
<div class="foot-head" style="left:552px;top:3532px">MENUS</div>
<div class="foot-link" style="top:3570px">Home</div>
<div class="foot-link" style="top:3596px">About Us</div>
<div class="foot-link" style="top:3622px">FAQ</div>
<div class="foot-link" style="top:3648px">Resources</div>
<div class="foot-link" style="top:3675px">Contact</div>
<div class="foot-head" style="left:747px;top:3532px">SIGN UP TO OUR NEWSLETTER</div>
<p class="abs" style="left:748px;top:3570px;font:400 13px var(--body);color:#333">Sed ut perspiciatis unde omnis iste natus</p>
<div class="abs" style="left:748px;top:3609px;width:306px;height:42px;border:1px solid #bfc3c8;border-radius:22px;padding:13px 22px;font:400 12px var(--body);color:#333">Enter Email</div>
<div class="btn" style="left:748px;top:3665px;width:306px;height:41px;font-size:15px;font-weight:700">SIGN UP</div>
<p class="abs" style="left:0;top:3771px;width:1200px;text-align:center;font:400 13px var(--body);color:#333">© 2025 &nbsp;Keystone Financial Services- All Rights Reserved &nbsp;| &nbsp;Privacy Policy &nbsp;| &nbsp;Terms of use</p>
<p class="abs" style="left:160px;top:3811px;width:880px;text-align:center;font:400 11px/17px var(--body);color:#555">Sed ut perspiciatis unde omnis iste natus error sit voluptatem accusantium doloremque laudantium, totam rem aperiam, eaque ipsa quae ab illo inventore veritatis et quasi architecto beatae vitae dicta sunt explicabo. Nemo enim ipsam voluptatem quia voluptas sit aspernatur aut odit</p>
<span class="card-chip" style="left:425px;background:#d7deea"></span>
<span class="card-chip" style="left:465px;background:#e8dcd0"></span>
<span class="card-chip" style="left:505px;background:#e3e3e3"></span>
<span class="card-chip" style="left:545px;background:#cfe2f2"></span>
<span class="card-chip" style="left:585px;background:#dde4f0"></span>
<span class="soc" style="left:646px;background:var(--blue)"></span>
<span class="soc" style="left:692px;background:var(--pink)"></span>
<span class="soc" style="left:738px;background:var(--blue)"></span>

</body>
</html>
```